Fun relaxed Travel Photography Business Card*

Require a fun, funky and quirky but rememberable business card for a travel photographer

Industry/Entity Type

Photographer

Contact Information for Business Card

Front Card

(my name) Lenn D.

Travel Photographer ( small under travel photographer) “self-proclaimed”

(website logo) wanderingsoflenn.net

(Instagram logo) @wanderings_of_lenn

(Instagram logo) @wanderings_of_lenn_2.0 (backup for when Instagram puts Lenn on timeout for bad behaviour)

Tel: N/A (removing the potential awkwardness of me not replying)

Email: (see above)

Back Card

Offending people since 1986

(Bottom right corner) “p.s. travelling made me fatTER”

Font styles to use
Serif

Colors

Designer to choose colors to be used in the design.

Requirements
Must have
• a camera
• a similar cartoon version of me as the "logo" see attached files, try to make as similar as possible

```html
<!DOCTYPE html>
<html lang="en">
<head>
<meta charset="utf-8">
<title>Lenn D. – Travel Photographer Business Card</title>
<link rel="stylesheet" href="https://fonts.googleapis.com/css2?family=Zilla+Slab:ital,wght@0,300;0,400;0,700;1,400&display=swap">
<style>
  :root {
    --backdrop: #8c8c8c;
    --card-light: #ffffff;
    --card-dark: #0b0b0b;
    --pattern-tone: #1d1d1d;
    --ink: #111111;
    --paper: #ffffff;
    --rule: #9a9a9a;
    --muted: #dcdcdc;
  }
  * { margin: 0; padding: 0; box-sizing: border-box; }
  html, body { width: 1200px; height: 1200px; overflow: hidden; }
  body {
    background: var(--backdrop);
    font-family: "Zilla Slab", Georgia, serif;
    position: relative;
  }
  .card {
    position: absolute;
    top: 310px;
    height: 594px;
    box-shadow: 0 3px 8px rgba(0,0,0,0.35);
  }
  .card--front { left: 234px; width: 364px; background: var(--card-light); color: var(--ink); }
  .card--back  { left: 627px; width: 370px; background: var(--card-dark); color: var(--paper); overflow: hidden; }

  .pattern {
    position: absolute; inset: 0;
    background: radial-gradient(circle at 50% 50%, var(--pattern-tone) 0%, #131313 60%, var(--card-dark) 100%);
  }

  .brand { position: absolute; }
  .card--front .brand { left: 62px; top: 150px; }
  .card--back .brand  { left: 46px; top: 236px; }
  .brand__row { display: flex; align-items: center; gap: 14px; }
  .brand__dot {
    width: 52px; height: 52px; border-radius: 50%;
    border: 3px solid currentColor;
  }
  .brand__name {
    font-weight: 400; font-size: 52px; line-height: 1; letter-spacing: 0.5px;
  }
  .brand__role {
    margin-left: 82px; margin-top: 4px;
    font-weight: 700; font-size: 14px; letter-spacing: 0.6px;
  }
  .brand__tag {
    margin-left: 82px; margin-top: 2px;
    display: flex; align-items: center; gap: 6px;
    font-weight: 700; font-style: italic; font-size: 9px; letter-spacing: 0.8px;
  }
  .brand__tag::before, .brand__tag::after {
    content: ""; height: 2px; width: 14px; background: currentColor;
  }

  .divider { position: absolute; left: 88px; width: 188px; height: 24px; }
  .divider--contact { top: 342px; }
  .divider--social  { top: 465px; }

  .contact {
    position: absolute; left: 0; width: 100%;
    text-align: center; font-size: 17px; line-height: 22px;
  }
  .contact--main   { top: 386px; }
  .contact--social { top: 493px; }

  .quip {
    position: absolute;
    font-size: 15px; letter-spacing: 0.4px; color: var(--muted);
  }
  .quip--since { top: 482px; left: 60px; }
  .quip--ps    { top: 523px; left: 52px; font-style: italic; }
</style>
</head>
<body>

  <section class="card card--front" aria-label="Front of card">
    <div class="brand">
      <div class="brand__row">
        <span class="brand__dot"></span>
        <span class="brand__name">Lenn D</span>
      </div>
      <div class="brand__role">TRAVEL PHOTOGRAPHER</div>
      <div class="brand__tag">SELF-PROCLAIMED</div>
    </div>

    <svg class="divider divider--contact" viewBox="0 0 188 24" aria-hidden="true">
      <line x1="0" y1="12" x2="188" y2="12" stroke="var(--rule)" stroke-width="1"/>
      <circle cx="66" cy="12" r="11" fill="var(--ink)"/>
      <rect x="59" y="8" width="14" height="9" rx="1.5" fill="none" stroke="#fff" stroke-width="1.3"/>
      <rect x="63" y="6" width="5" height="2.5" fill="#fff"/>
      <circle cx="66" cy="12.5" r="2.6" fill="none" stroke="#fff" stroke-width="1.2"/>
      <circle cx="93" cy="12" r="11" fill="var(--ink)"/>
      <rect x="87" y="8" width="12" height="8" fill="none" stroke="#fff" stroke-width="1.3"/>
      <path d="M87 8 l6 5 l6 -5" fill="none" stroke="#fff" stroke-width="1.3"/>
      <circle cx="121" cy="12" r="11" fill="var(--ink)"/>
      <circle cx="121" cy="12" r="6" fill="none" stroke="#fff" stroke-width="1.3"/>
      <line x1="115" y1="12" x2="127" y2="12" stroke="#fff" stroke-width="1"/>
      <ellipse cx="121" cy="12" rx="2.5" ry="6" fill="none" stroke="#fff" stroke-width="1"/>
    </svg>

    <div class="contact contact--main">
      <p>info@wanderingsoflenn.net</p>
      <p>www.wanderingsoflenn.net</p>
    </div>

    <svg class="divider divider--social" viewBox="0 0 188 24" aria-hidden="true">
      <line x1="0" y1="12" x2="188" y2="12" stroke="var(--rule)" stroke-width="1"/>
      <circle cx="94" cy="12" r="11" fill="var(--ink)"/>
    </svg>

    <div class="contact contact--social">
      <p>@wanderings_of_lenn</p>
      <p>@wanderings_of_lenn_2.0</p>
    </div>
  </section>

  <section class="card card--back" aria-label="Back of card">
    <div class="pattern" role="img" aria-label="Faint repeating pattern of cameras, film reels and photographers"></div>
    <div class="brand">
      <div class="brand__row">
        <span class="brand__dot"></span>
        <span class="brand__name">Lenn D</span>
      </div>
      <div class="brand__role">TRAVEL PHOTOGRAPHER</div>
      <div class="brand__tag">SELF-PROCLAIMED</div>
    </div>
    <p class="quip quip--since">OFFENDING PEOPLE SINCE 1986</p>
    <p class="quip quip--ps">P.S. TRAVELLING MADE ME FATTER</p>
  </section>

</body>
</html>
```